Logo, Web and Mobile Designs for enterprise social media platform

All the details are in the attached document, please start reading the scope document first which explains what is this project about and the details about the needed deliverables, after that please read the UI_Requirements document which will detail what is expected regarding the coded web version since this is a coded contest, it is very important that you meet the UI requirements or suggest something else but we will need to agree first before working on the coded version

Good Luck

Target Market(s)

Enterprise Social Media

Industry/Entity Type

Media

Coding

Coded - Design and coding required

Number of Pages Required

5+ page

Font styles to use
Sans Serif

Requirements
Must have
• All the must haves are listed in the scope document so please check before you start

```html
<!DOCTYPE html>
<html lang="en">
<head>
<meta charset="utf-8">
<title>Teamora – Create New Business Opportunity</title>
<link href="https://fonts.googleapis.com/css2?family=Roboto:wght@300;400;500&display=swap" rel="stylesheet">
<style>
:root{
  --page-bg:#ebebeb;
  --white:#ffffff;
  --header-bg:#f9f9f9;
  --line:#dcdcdc;
  --text:#555a60;
  --text-dark:#3f4348;
  --icon:#6b6f75;
  --brand-blue:#2a9bd0;
  --brand-orange:#f29d12;
  --badge-orange:#f5a20f;
  --badge-blue:#2a9bd0;
  --button:#ea9500;
  --button-edge:#c57c00;
  --footer:#1e8bb5;
  --panel-head:#f6f7f9;
}
*{box-sizing:border-box;margin:0;padding:0}
html,body{width:1200px;height:820px;overflow:hidden}
body{background:var(--page-bg);font-family:'Roboto',sans-serif;color:var(--text);position:relative}

.topbar{position:absolute;left:0;top:0;width:1200px;height:70px;background:var(--header-bg);border-bottom:1px solid var(--line)}
.topbar .menu-btn{position:absolute;left:100px;top:29px}
.topbar .divider{position:absolute;top:0;width:1px;height:70px;background:var(--line)}
.brand{position:absolute;left:171px;top:16px;display:flex;align-items:center;gap:9px}
.brand .mark{width:36px;height:36px;border-radius:50%;background:var(--brand-orange)}
.brand .name{font-size:30px;font-weight:500;color:var(--brand-blue);letter-spacing:.3px}
.user{position:absolute;left:746px;top:20px;display:flex;align-items:center}
.user .avatar{width:34px;height:34px;border-radius:50%;background:radial-gradient(circle at 50% 40%,#8a7a70,#2f2b2a)}
.user .uname{margin-left:12px;font-size:17px;font-weight:300;color:var(--text-dark)}
.user svg{margin-left:13px}
.tool{position:absolute;top:24px}
.badge{position:absolute;top:16px;height:16px;min-width:20px;padding:0 5px;border-radius:8px;color:#fff;font-size:11px;line-height:16px;text-align:center}

.panel{position:absolute;left:99px;top:111px;width:1001px;height:520px;background:var(--white);border:1px solid #e2e2e2}
.panel-head{height:48px;background:var(--panel-head);border-bottom:1px solid #e2e2e2;position:relative}
.panel-head h1{position:absolute;left:19px;top:15px;font-size:15.5px;font-weight:400;color:var(--text-dark);letter-spacing:-.1px}
.panel-head svg{position:absolute;right:30px;top:19px}
.label{position:absolute;left:36px;font-size:14.5px;font-weight:300;color:var(--text-dark)}
.field{position:absolute;left:208px;width:468px;border:1px solid #dedede;background:#fff;font-size:12.5px;color:var(--text-dark)}
.field span{position:absolute;left:22px;top:13px}
.select .chev{position:absolute;right:0;top:0;width:38px;height:100%;border-left:1px solid #dedede;display:flex;align-items:center;justify-content:center}
.radios{position:absolute;left:208px;top:396px;display:flex;align-items:center;font-size:12.5px;color:var(--text-dark)}
.radio{width:15px;height:15px;border-radius:50%;border:1px solid #cfcfcf;background:#f4f4f4;margin-right:11px;position:relative}
.radio.on::after{content:"";position:absolute;left:5px;top:5px;width:3px;height:3px;border-radius:50%;background:#777}
.btn-primary{position:absolute;left:208px;top:437px;width:234px;height:36px;background:var(--button);border-bottom:2px solid var(--button-edge);border-radius:2px;color:#fff;font-size:16px;font-weight:500;text-align:center;line-height:35px;letter-spacing:.2px}

.footer{position:absolute;left:0;top:672px;width:1200px;height:148px;background:var(--footer);color:#fff;text-align:center}
.social{position:absolute;left:513px;top:29px;display:flex;gap:13px}
.social span{width:24px;height:24px;border-radius:4px;background:#fff}
.links{position:absolute;left:0;width:100%;top:71px;font-size:14.5px;font-weight:300}
.links i{font-style:normal;margin:0 10px}
.copy{position:absolute;left:0;width:100%;top:102px;font-size:14.5px}
</style>
</head>
<body>

<header class="topbar">
  <svg class="menu-btn" width="19" height="15" viewBox="0 0 19 15"><rect width="19" height="3" fill="#6b6f75"/><rect y="6" width="19" height="3" fill="#6b6f75"/><rect y="12" width="19" height="3" fill="#6b6f75"/></svg>
  <div class="divider" style="left:145px"></div>
  <div class="brand"><span class="mark"></span><span class="name">Teamora</span></div>
  <div class="user">
    <div class="avatar" role="img" aria-label="User profile photo"></div>
    <span class="uname">Alex Moreno</span>
    <svg width="12" height="7" viewBox="0 0 12 7"><path d="M0 0h12L6 7z" fill="#4a4e53"/></svg>
  </div>
  <div class="divider" style="left:922px"></div>
  <svg class="tool" style="left:945px" width="20" height="20" viewBox="0 0 20 20"><rect x="0" y="1" width="20" height="4" fill="#6b6f75"/><rect x="0" y="8" width="9" height="4" fill="#6b6f75"/><rect x="11" y="8" width="9" height="4" fill="#6b6f75"/><rect x="0" y="15" width="9" height="4" fill="#6b6f75"/><rect x="11" y="15" width="9" height="4" fill="#9a9ea3"/></svg>
  <span class="badge" style="left:956px;background:var(--badge-orange)">8</span>
  <div class="divider" style="left:991px"></div>
  <svg class="tool" style="left:1011px" width="20" height="20" viewBox="0 0 20 20"><circle cx="8" cy="8" r="6" fill="none" stroke="#6b6f75" stroke-width="3"/><path d="M12.5 12.5l6 6" stroke="#6b6f75" stroke-width="3.4" stroke-linecap="round"/></svg>
  <div class="divider" style="left:1051px"></div>
  <svg class="tool" style="left:1072px" width="20" height="22" viewBox="0 0 20 22"><path d="M10 1c-4 0-6 3-6 7v5l-3 3v1h18v-1l-3-3V8c0-4-2-7-6-7z" fill="#6b6f75"/><path d="M7 19a3 3 0 006 0z" fill="#6b6f75"/></svg>
  <span class="badge" style="left:1078px;background:var(--badge-blue)">8</span>
</header>

<main class="panel">
  <div class="panel-head">
    <h1>CREATE NEW BUSINESS OPPORTUNITY - STEP 1</h1>
    <svg width="7" height="11" viewBox="0 0 7 11"><path d="M1 1l4.5 4.5L1 10" fill="none" stroke="#aaa" stroke-width="1.8"/></svg>
  </div>

  <label class="label" style="top:96px">Name : *</label>
  <div class="field" style="top:84px;height:38px"></div>

  <label class="label" style="top:150px">Description : *</label>
  <div class="field" style="top:138px;height:125px"></div>

  <label class="label" style="top:289px">Choose Network : *</label>
  <div class="field select" style="top:278px;height:38px">
    <span>Create New</span>
    <div class="chev"><svg width="9" height="6" viewBox="0 0 9 6"><path d="M1 1l3.5 3.5L8 1" fill="none" stroke="#555" stroke-width="1.4"/></svg></div>
  </div>
  <div class="field" style="top:323px;height:38px"><span>Enter the new network name</span></div>

  <label class="label" style="top:396px">Comments Visibility : *</label>
  <div class="radios">
    <span class="radio"></span><span>Public</span>
    <span class="radio on" style="margin-left:32px"></span><span>Private</span>
  </div>

  <div class="btn-primary">SAVE AND GO TO STEP 2</div>
</main>

<footer class="footer">
  <div class="social" aria-label="Social links">
    <span></span><span></span><span></span><span></span><span></span>
  </div>
  <nav class="links">Home<i>/</i>Contact<i>/</i>Topics<i>/</i>Posts and Comments<i>/</i>Discussion<i>/</i>Videos Links</nav>
  <p class="copy">Copyright @ 2015 - 2015.Teamora. All Rights Reserved.</p>
</footer>

</body>
</html>
```